Card and board game developer website, small e-commerce site

We are designing a website for Leaping Otter Engine Works. I need a homepage and a typical inside page designed.
The website navigation will be:
Home (where we'll introduce the games and the website)
Our Games (drops open into the two games)
Griffins of Marrowvale
Tidebound
Order Now
About Us
Contact
The header of the website will include the logo, the navigation and a link to a facebook page. The header will also include a cart icon and a link to My Account.
Then on the homepage I suggest we include a row for each game:
Griffins of Marrowvale
This row will include a photo (or maybe a series of photos that animate into each other) and quick info about the game plus two buttons: Info and Photos (which will go to the detail page with the photo gallery), and Order Now (which will take you to the product for ordering).
Tidebound
Your footer will contain a copyright note, plus links to:
Terms and conditions
Shipping and returns
FAQ
Contact
Account login
NOTE: the logo is the orange mokey. I've uploaded a brief with more information. The current website that we are redesigning is here https://www.leapingotterengine.example/
Please send me any questions that you have.
Target Market(s)
People interested in fun card and board games at home.

```html
<!DOCTYPE html>
<html lang="en">
<head>
<meta charset="utf-8">
<title>Leaping Otter Engine Works</title>
<link rel="stylesheet" href="https://fonts.googleapis.com/css2?family=Titillium+Web:wght@600;700;900&family=Lato:wght@400;700&family=Roboto:wght@400;500&display=swap">
<style>
:root{
  --orange:#f08322;
  --orange-deep:#e8701a;
  --ink:#222;
  --text:#333;
  --hero-bg:#f2f2f2;
  --white:#fff;
  --black:#000;
}
*{box-sizing:border-box;margin:0;padding:0}
html,body{width:1200px;height:3275px;overflow:hidden;background:var(--white)}
body{position:relative;font-family:'Lato',sans-serif;color:var(--text)}
a{text-decoration:none}
.abs{position:absolute}

/* header */
.site-header{position:absolute;left:0;top:0;width:1200px;height:103px;background:var(--white);z-index:3}
.brand-disc{position:absolute;left:89px;top:0;width:181px;height:163px;border-radius:0 0 91px 91px;background:var(--white);z-index:4;display:flex;align-items:center;justify-content:center;text-align:center;padding:0 14px}
.brand-disc span{font-family:'Titillium Web',sans-serif;font-weight:700;font-size:17px;line-height:1.15;color:var(--orange)}
.nav a{position:absolute;top:49px;font-family:'Roboto',sans-serif;font-size:15.5px;color:var(--text)}
.nav .caret{display:inline-block;width:8px;height:8px;border-right:2px solid #aaa;border-bottom:2px solid #aaa;transform:rotate(45deg);margin-left:8px;position:relative;top:-3px}
.divider{position:absolute;left:850px;top:43px;width:2px;height:32px;background:var(--orange)}
.icon-circle{position:absolute;border-radius:50%}
.account-label{position:absolute;left:970px;top:45px;font-family:'Titillium Web',sans-serif;font-weight:700;font-size:15px;color:var(--ink)}

/* hero */
.hero{position:absolute;left:0;top:103px;width:1200px;height:500px;overflow:hidden}
.hero-title{position:absolute;left:110px;font-family:'Titillium Web',sans-serif;font-weight:900;font-size:62px;line-height:86px;color:var(--orange);text-shadow:2px 2px 0 #3a2210;letter-spacing:.5px}
.hero-copy{position:absolute;left:114px;width:370px;font-size:16px;line-height:26px;color:var(--text)}
.btn{position:absolute;display:flex;align-items:center;justify-content:center;border-radius:28px;font-family:'Lato',sans-serif;font-weight:700;font-size:15px}
.btn-solid{background:var(--orange);color:var(--white)}
.btn-outline{border:2px solid var(--orange);color:var(--orange);background:transparent}
.btn-white{background:var(--white);color:var(--orange)}
.btn-ghost{border:2px solid var(--white);color:var(--white)}
.chev{display:inline-block;width:6px;height:6px;border-right:1.5px solid currentColor;border-bottom:1.5px solid currentColor;transform:rotate(45deg);margin-left:8px;position:relative;top:-2px}
.media{position:absolute}
.dot{position:absolute;top:660px;width:13px;height:13px;border-radius:50%;border:2px solid #333}
.dot.active{border-color:var(--orange)}

/* sections */
.section-title{position:absolute;left:0;width:1200px;text-align:center;font-family:'Titillium Web',sans-serif;font-weight:700;font-size:34px;letter-spacing:.5px}
.card{position:absolute;background:var(--white);box-shadow:0 2px 8px rgba(0,0,0,.15);padding:7px}
.card .media{position:static;width:100%;height:100%}
.arrow{position:absolute;width:44px;height:44px;border-radius:50%;display:flex;align-items:center;justify-content:center}
.game-copy{position:absolute;left:110px;top:1186px;width:960px;font-size:15.5px;line-height:24.5px;color:var(--text)}
.tide-band{position:absolute;left:0;top:1518px;width:1200px;height:685px;background:radial-gradient(ellipse at 30% 40%,#f7a64a 0%,#f28a28 45%,#ee7a1c 100%)}
.tide-copy{position:absolute;left:155px;top:1930px;width:890px;text-align:center;color:var(--white);font-size:15.5px;line-height:25.5px}

/* about */
.about-title{position:absolute;left:670px;top:2340px;font-family:'Titillium Web',sans-serif;font-weight:700;font-size:34px;color:var(--ink)}
.about-copy{position:absolute;left:670px;top:2413px;width:420px;text-align:justify;font-size:15.5px;line-height:25.7px;color:#444}

/* footer */
.footer-brand{position:absolute;left:0;top:2990px;width:1200px;text-align:center;font-family:'Titillium Web',sans-serif;font-weight:700;font-size:20px;color:var(--white)}
.footer-links{position:absolute;top:3092px;font-family:'Roboto',sans-serif;font-size:16px;color:var(--white)}
.copyright{position:absolute;left:0;top:3207px;width:1200px;text-align:center;font-family:'Roboto',sans-serif;font-size:16px;color:var(--white)}
</style>
</head>
<body>

<svg class="abs" style="left:0;top:0" width="1200" height="740" aria-hidden="true">
  <path d="M0 103 H1200 V616 Q600 800 0 616 Z" fill="#f2f2f2"/>
  <path d="M0 616 Q600 840 1200 616" fill="none" stroke="#f08322" stroke-width="7"/>
</svg>

<header class="site-header">
  <nav class="nav">
    <a style="left:341px" href="#">Home</a>
    <a style="left:419px" href="#">Our Games<span class="caret"></span></a>
    <a style="left:533px" href="#">Order Now<span class="caret"></span></a>
    <a style="left:643px" href="#">About Us</a>
    <a style="left:744px" href="#">Contact</a>
  </nav>
  <div class="divider"></div>
  <span class="icon-circle" style="left:880px;top:41px;width:30px;height:30px;background:var(--orange)" aria-label="Social page"></span>
  <svg class="abs" style="left:927px;top:39px" width="32" height="32" aria-label="Account">
    <circle cx="16" cy="16" r="14" fill="none" stroke="#f08322" stroke-width="2"/>
    <circle cx="16" cy="13" r="4.5" fill="#f08322"/>
    <path d="M8 23 Q16 15 24 23" fill="#f08322"/>
  </svg>
  <span class="account-label">ACCOUNT</span>
  <svg class="abs" style="left:1052px;top:36px" width="38" height="36" aria-label="Cart">
    <circle cx="16" cy="20" r="15" fill="#f08322"/>
    <path d="M9 16 H23 L21 25 H11 Z" fill="#fff"/>
    <path d="M12 16 L15 11 M20 16 L17 11" stroke="#fff" stroke-width="1.6"/>
    <circle cx="31" cy="7" r="5" fill="#fff" stroke="#f08322"/>
    <text x="31" y="10" font-size="8" text-anchor="middle" fill="#333" font-family="Roboto,sans-serif">0</text>
  </svg>
</header>
<div class="brand-disc"><span>Leaping Otter Engine Works</span></div>

<section class="hero" aria-label="Introduction">
  <h1 class="hero-title" style="top:119px">LEAPING OTTER<br>ENGINE WORKS</h1>
  <p class="hero-copy" style="top:297px">Lorem ipsum dolor sit amet, consectetur adipiscing elit, sed do eiusmod tempor incididunt ut labore et dolore magna aliqua.</p>
  <a class="btn btn-outline" style="left:112px;top:399px;width:141px;height:54px" href="#">Order Now<span class="chev"></span></a>
  <div class="media" role="img" aria-label="Board game laid out with hex map, cards, dice and coin pouch" style="left:590px;top:100px;width:600px;height:380px;background:radial-gradient(closest-side,#6f8f3a 0%,#4d6b2c 60%,rgba(242,242,242,0) 100%)"></div>
</section>
<span class="dot" style="left:576px"></span>
<span class="dot active" style="left:594px"></span>
<span class="dot" style="left:612px"></span>

<h2 class="section-title" style="top:822px;color:var(--ink)">GRIFFINS OF MARROWVALE</h2>
<div class="card" style="left:121px;top:910px;width:208px;height:224px"><div class="media" role="img" aria-label="Game box and pouch" style="background:linear-gradient(135deg,#fff 30%,#8a4a3c 55%,#3a3436 80%)"></div></div>
<div class="card" style="left:374px;top:910px;width:208px;height:224px"><div class="media" role="img" aria-label="Pale creature over ice peaks" style="background:linear-gradient(160deg,#dde9ee,#b9d4dc 50%,#ecd2cf)"></div></div>
<div class="card" style="left:627px;top:910px;width:208px;height:224px"><div class="media" role="img" aria-label="Dark creature in night shadow" style="background:linear-gradient(160deg,#3a4250,#1c2029 60%,#2a2630)"></div></div>
<div class="card" style="left:880px;top:910px;width:208px;height:224px"><div class="media" role="img" aria-label="Blue creature on a purple bloom" style="background:linear-gradient(180deg,#4f6a8a,#4a58b0 55%,#a6508f)"></div></div>
<span class="arrow" style="left:55px;top:1000px;background:var(--orange)"><svg width="20" height="14"><path d="M19 7 H2 M8 1 L2 7 L8 13" stroke="#fff" stroke-width="2" fill="none"/></svg></span>
<span class="arrow" style="left:1104px;top:1000px;background:var(--white);box-shadow:0 1px 6px rgba(0,0,0,.2)"><svg width="20" height="14"><path d="M1 7 H18 M12 1 L18 7 L12 13" stroke="#f08322" stroke-width="2" fill="none"/></svg></span>
<p class="game-copy">Welcome to The Griffins Of Marrowvale, the first board game where every player is a GRIFFIN. Conquer territory and build your empire. Plunder castles and collect a huge hoard of gold. Rescue relatively attractive royalty or maybe eat them.&nbsp; Who knows?&nbsp; All we know is that everyone's a winner when the pizza's delivered!**<br>2 - 6 players *<br>Playtime approximately 1.5 hours.<br>* Game comes with 4 griffin packs.&nbsp; Additional griffin expansion packs coming soon.</p>
<a class="btn btn-solid" style="left:110px;top:1373px;width:147px;height:52px" href="#">Info and Photos</a>
<a class="btn btn-outline" style="left:267px;top:1372px;width:141px;height:54px" href="#">Order Now<span class="chev"></span></a>

<section class="tide-band" aria-label="Tidebound"></section>
<h2 class="section-title" style="top:1567px;color:var(--white)">TIDEBOUND</h2>
<div class="media" role="img" aria-label="Card deck box" style="left:112px;top:1655px;width:226px;height:224px;border-radius:6px;background:radial-gradient(circle at 50% 50%,#7a3a22 0%,#3a2a24 40%,#fff 62%)"></div>
<div class="media" role="img" aria-label="Fire element card art" style="left:362px;top:1655px;width:226px;height:224px;border-radius:6px;background:linear-gradient(180deg,#f6e2c2,#f08a2c 55%,#d84a1e)"></div>
<div class="media" role="img" aria-label="Guardian card art" style="left:611px;top:1655px;width:227px;height:224px;border-radius:6px;background:linear-gradient(180deg,#f3e3c6,#e79a6a 55%,#c8302a)"></div>
<div class="media" role="img" aria-label="Water element card art" style="left:862px;top:1655px;width:226px;height:224px;border-radius:6px;background:linear-gradient(180deg,#f4ead6,#6ac4a4 55%,#e88a3a)"></div>
<span class="arrow" style="left:54px;top:1745px;border:2px solid var(--white)"><svg width="20" height="14"><path d="M19 7 H2 M8 1 L2 7 L8 13" stroke="#fff" stroke-width="2" fill="none"/></svg></span>
<span class="arrow" style="left:1104px;top:1745px;background:var(--white)"><svg width="20" height="14"><path d="M1 7 H18 M12 1 L18 7 L12 13" stroke="#f08322" stroke-width="2" fill="none"/></svg></span>
<p class="tide-copy">Welcome to Tidebound, a fast paced card game of strategy and chance.&nbsp; Play your element cards (Earth, Air, Fire,Water) and wild cards (Guardian, Balance, Evolution, Genesis) wisely and be the first player to discard all of their cards and declare yourself the master of the elements.<br><span style="display:block;margin-top:15px">Coming to Backerhall soon</span></p>
<a class="btn btn-white" style="left:461px;top:2090px;width:145px;height:53px" href="#">Info and Photos</a>
<a class="btn btn-ghost" style="left:618px;top:2089px;width:131px;height:55px" href="#">Order Now<span class="chev"></span></a>

<svg class="abs" style="left:115px;top:2293px" width="474" height="474" aria-hidden="true">
  <circle cx="236" cy="234" r="229" fill="#f08322"/>
</svg>
<div class="media" role="img" aria-label="Player board and dice on a velvet pouch" style="left:130px;top:2305px;width:456px;height:450px;border-radius:50%;background:radial-gradient(circle at 40% 55%,#6a3a34 0%,#3d3436 45%,#e8e8e8 75%)"></div>
<h2 class="about-title">ABOUT US</h2>
<p class="about-copy">Lorem ipsum dolor sit amet, consectetur adipiscing elit, sed do eiusmod tempor incididunt ut labore et dolore magna aliqua. Ut enim ad minim veniam, quis nostrud exercitation ullamco laboris nisi ut aliquip ex ea commodo consequat. Duis aute irure dolor in reprehenderit in voluptate velit esse cillum dolore eu fugiat nulla pariatur. Excepteur sint occaecat cupidatat non proident, sunt in culpa qui officia deserunt mollit anim id est laborum.</p>
<a class="btn btn-solid" style="left:670px;top:2651px;width:126px;height:51px" href="#">Read More</a>

<svg class="abs" style="left:0;top:2830px" width="1200" height="445" aria-hidden="true">
  <path d="M0 120 Q600 -100 1200 120 V445 H0 Z" fill="#000"/>
  <path d="M0 120 Q600 -100 1200 120" fill="none" stroke="#f08322" stroke-width="7"/>
</svg>
<footer>
  <div class="footer-brand">Leaping Otter<br>Engine Works</div>
  <a class="footer-links" style="left:297px" href="#">Terms and conditions</a>
  <a class="footer-links" style="left:480px" href="#">Shipping and returns</a>
  <a class="footer-links" style="left:656px" href="#">FAQ</a>
  <a class="footer-links" style="left:720px" href="#">Contact</a>
  <a class="footer-links" style="left:808px" href="#">Account login</a>
  <span class="icon-circle" style="left:581px;top:3148px;width:38px;height:38px;border:2px solid var(--orange)" aria-label="Social page"></span>
  <p class="copyright">©Copyrights 2024 Leaping Otter Engine Works&nbsp;&nbsp; |&nbsp;&nbsp;&nbsp; All Rights Reserved</p>
</footer>

</body>
</html>
```